Corvel Capital LLC

Need Professional Business cards for New Investment Fund

Target Market(s)

High Quality investors

Industry/Entity Type

Financial

Contact Information for Business Card

Phone Number +1 555 284 6190
Name Lukas Varenko
Title Fund Manager
email lv@FundCorvel.com
Website www.FundCorvel.com

Colors

Designer to choose colors to be used in the design.

Requirements
Must have
• Must have our Logo and all of the above. Must be made so lettering and loge can be raised

```html
<!DOCTYPE html>
<html lang="en">
<head>
<meta charset="utf-8">
<title>Lukas Varenko – Business Card</title>
<link rel="stylesheet" href="https://fonts.googleapis.com/css2?family=Lato:wght@400;700&display=swap">
<style>
  :root {
    --page-bg: #e8e8e5;
    --panel-dark: #404b41;
    --accent-green: #22e012;
    --card-light: #f7f7f6;
    --text-light: #ffffff;
    --brand-ink: #3f4a40;
  }
  * { box-sizing: border-box; margin: 0; padding: 0; }
  html, body {
    width: 1200px;
    height: 900px;
    overflow: hidden;
    background: var(--page-bg);
    font-family: "Lato", sans-serif;
  }
  .business-card {
    position: absolute;
    left: 145px;
    top: 166px;
    width: 910px;
    height: 567px;
    display: flex;
    background: var(--card-light);
    box-shadow: 0 6px 24px rgba(0, 0, 0, 0.12);
  }
  .contact-panel {
    position: relative;
    width: 437px;
    height: 100%;
    background: var(--panel-dark);
    border-right: 7px solid var(--accent-green);
    color: var(--text-light);
  }
  .holder-name {
    position: absolute;
    left: 52px;
    top: 72px;
    font-weight: 700;
    font-size: 31px;
    letter-spacing: 0.5px;
    text-transform: uppercase;
    color: var(--accent-green);
    line-height: 1;
  }
  .holder-title {
    position: absolute;
    left: 52px;
    top: 112px;
    font-weight: 400;
    font-size: 24px;
    line-height: 1;
  }
  .contact-list {
    position: absolute;
    left: 52px;
    top: 390px;
    list-style: none;
  }
  .contact-item {
    display: flex;
    align-items: center;
    gap: 9px;
    height: 34px;
    font-size: 24px;
    line-height: 1;
  }
  .contact-icon {
    width: 20px;
    height: 20px;
    flex: none;
    fill: var(--accent-green);
  }
  .brand-side {
    flex: 1;
    display: flex;
    align-items: center;
    justify-content: center;
  }
  .brand-mark {
    display: flex;
    align-items: center;
    gap: 14px;
    color: var(--brand-ink);
    font-weight: 700;
    font-size: 44px;
    letter-spacing: 2px;
    text-transform: uppercase;
  }
  .brand-square {
    width: 30px;
    height: 30px;
    background: var(--accent-green);
  }
</style>
</head>
<body>
  <main class="business-card">
    <section class="contact-panel">
      <h1 class="holder-name">Lukas Varenko</h1>
      <p class="holder-title">Fund Manager</p>
      <ul class="contact-list">
        <li class="contact-item">
          <svg class="contact-icon" viewBox="0 0 20 20" aria-hidden="true">
            <path d="M2 7c0-3 3-4 8-4s8 1 8 4v1h-4V6H6v2H2z"/>
            <path d="M5 10l2-3h6l2 3v7H5z"/>
          </svg>
          <span>+1 555 284 6190</span>
        </li>
        <li class="contact-item">
          <svg class="contact-icon" viewBox="0 0 20 20" aria-hidden="true">
            <path d="M2 4h16v1.5L10 11 2 5.5z"/>
            <path d="M2 7.5l8 5.5 8-5.5V16H2z"/>
          </svg>
          <span>lv@FundCorvel.com</span>
        </li>
        <li class="contact-item">
          <svg class="contact-icon" viewBox="0 0 20 20" aria-hidden="true">
            <circle cx="10" cy="10" r="8.5"/>
            <path d="M6 6c2 0 3 1 3 3s-2 2-2 4 1 3 1 3" stroke="#404b41" stroke-width="1.6" fill="none"/>
            <path d="M13 5c-1 2 1 3 2 4" stroke="#404b41" stroke-width="1.6" fill="none"/>
          </svg>
          <span>www.FundCorvel.com</span>
        </li>
      </ul>
    </section>
    <section class="brand-side">
      <div class="brand-mark">
        <span class="brand-square"></span>
        <span class="brand-name">Orvessa</span>
      </div>
    </section>
  </main>
</body>
</html>
```